Policies Manual Design & Formatting

My company currently has complete bylaws and policies organized as needed. We would like them formatted in Word to look professional and easily editable.

We have all text and titles completed and a brand book to guide text and colors. We would also like the designer to gather design inspiration from our website brackenvalecouncil.org.

Text word file upload coming on 10/18
Updates

Went on vacation/holiday

Industry/Entity Type

Business Consultant

Font styles to use
Serif
Sans Serif
Other font styles liked:
• Montserrat and Domine

Colors

Designer to choose colors to be used in the design.

Requirements
Must have
• Montserrat and domine fonts
• Colors from brand book file
• layout and print formatting
• dynamic Table of Contents
• Incorporate logo and company information
• Include automatic page numbers
• Modify or add headers/footer
• Profeasional cover page

```html
<!DOCTYPE html>
<html lang="en">
<head>
<meta charset="utf-8">
<title>Brackenvale Chamber Bylaws – Page Layouts</title>
<link rel="stylesheet" href="https://fonts.googleapis.com/css2?family=Montserrat:wght@400;500;600;700;800&family=Roboto+Condensed:wght@400&display=swap">
<style>
:root{
  --brand-blue:#0b8fcb;
  --brand-sky:#1bb2e6;
  --ink:#262626;
  --charcoal:#2a2a2c;
  --paper:#ffffff;
  --stage:#e6e6e6;
}
*{box-sizing:border-box;margin:0;padding:0}
html,body{width:852px;height:1200px;overflow:hidden;background:var(--stage)}
.sheet{position:relative;width:852px;height:1200px}
.page{position:absolute;width:378px;height:535px;background:var(--paper);overflow:hidden;font-family:'Montserrat',sans-serif;color:var(--ink)}
.page--cover{left:25px;top:17px}
.page--two{left:450px;top:17px}
.page--three{left:25px;top:611px}
.page--four{left:450px;top:611px}
.page-label{position:absolute;width:378px;text-align:center;font-family:'Roboto Condensed',sans-serif;font-size:19px;color:var(--ink);letter-spacing:.2px}
.page-label--top{top:566px}
.page-label--bottom{top:1160px}
.page-label--left{left:25px}
.page-label--right{left:450px}

/* cover */
.cover-art{position:absolute;inset:0}
.cover-url{position:absolute;left:0;width:230px;top:54px;text-align:center;color:#fff;font-family:'Roboto Condensed',sans-serif;font-weight:700;font-size:11px;letter-spacing:.2px}
.cover-globe{position:absolute;left:103px;top:31px}
.cover-name{position:absolute;left:18px;top:430px;width:140px;text-align:center;font-family:'Montserrat',sans-serif;font-weight:700;font-size:14px;line-height:18px;color:var(--ink)}

/* inner pages */
.top-band{position:absolute;left:26px;top:0;width:326px;height:15px;background:var(--brand-blue);border-radius:0 0 8px 8px}
.footer-band{position:absolute;left:26px;top:503px;width:326px;height:32px;background:var(--brand-blue);border-radius:8px 8px 0 0;color:#fff;font-size:6.6px;font-weight:700;display:flex;align-items:center;justify-content:space-between;padding:0 9px 0 8px}
.doc-title{position:absolute;left:0;width:378px;top:34px;text-align:center;font-weight:800;font-size:18.5px;letter-spacing:-.2px;color:var(--ink)}
.title-rule{position:absolute;left:105px;top:59px;width:168px;height:1px;background:var(--brand-blue)}
.title-rule--short{left:142px;top:63px;width:94px}
.ribbon{position:absolute;left:50%;transform:translateX(-50%);width:196px;height:28px}
.ribbon-text{position:absolute;inset:0;display:flex;align-items:center;justify-content:center;color:#fff;font-weight:600;font-size:11.5px;padding-bottom:2px}
.body{position:absolute;left:26px;width:326px;font-size:6.9px;line-height:9.1px;text-align:justify}
.section{margin-bottom:8px}
.section h3{font-size:6.9px;font-weight:600;line-height:9.1px}
.section p + p{margin-top:8px}
.points{list-style:none;margin:10px 0 10px 27px}
.points li{position:relative;margin-bottom:8px}
.points li::before{content:"";position:absolute;left:-8px;top:3px;width:3.4px;height:3.4px;border-radius:50%;background:var(--brand-blue)}
.points h4{color:var(--brand-blue);font-weight:600;font-size:6.9px}
.sub{margin-left:27px}
.sub h4{color:var(--brand-blue);font-weight:600;font-size:6.9px}
.tight{list-style:none;margin:8px 0 0 27px}
.tight li{position:relative;margin-bottom:2px}
.tight li::before{content:"";position:absolute;left:-8px;top:3px;width:3.4px;height:3.4px;border-radius:50%;background:var(--brand-blue)}
</style>
</head>
<body>
<div class="sheet">

  <!-- Cover -->
  <section class="page page--cover">
    <svg class="cover-art" width="378" height="535" viewBox="0 0 378 535">
      <polygon points="225,0 378,0 378,400 250,272 358,141" fill="var(--charcoal)"/>
      <polygon points="0,32 113,140 0,252" fill="var(--charcoal)"/>
      <polygon points="0,0 230,0 116,134 0,24" fill="var(--brand-blue)"/>
      <g role="img" aria-label="Photo of a town dairy sign topped with a cow statue">
        <polygon points="118,138 226,12 358,141 240,262" fill="#e9b889"/>
      </g>
      <g role="img" aria-label="Photo of a brick storefront with a pizza shop awning">
        <polygon points="4,256 116,144 238,265 130,388" fill="#5d7a86"/>
      </g>
      <g role="img" aria-label="Photo of a wooden hashtag sign beside evergreen shrubs">
        <polygon points="128,392 246,276 378,404 378,535 255,535" fill="#8a9388"/>
      </g>
    </svg>
    <svg class="cover-globe" width="24" height="24" viewBox="0 0 24 24" aria-hidden="true">
      <circle cx="12" cy="12" r="10" fill="none" stroke="#fff" stroke-width="2"/>
      <ellipse cx="12" cy="12" rx="4.5" ry="10" fill="none" stroke="#fff" stroke-width="1.6"/>
      <line x1="2" y1="12" x2="22" y2="12" stroke="#fff" stroke-width="1.6"/>
      <line x1="4" y1="7" x2="20" y2="7" stroke="#fff" stroke-width="1.4"/>
      <line x1="4" y1="17" x2="20" y2="17" stroke="#fff" stroke-width="1.4"/>
    </svg>
    <div class="cover-url">www.brackenvalecouncil.org</div>
    <div class="cover-name">Brackenvale Chamber of Commerce</div>
  </section>
  <div class="page-label page-label--top page-label--left">FRONT PAGE</div>

  <!-- Page 2 -->
  <section class="page page--two">
    <div class="top-band"></div>
    <h1 class="doc-title">BRACKENVALE CHAMBER BYLAWS</h1>
    <div class="title-rule"></div>
    <div class="title-rule title-rule--short"></div>
    <div class="ribbon" style="top:79px">
      <svg width="196" height="28" viewBox="0 0 196 28" aria-hidden="true">
        <polygon points="0,6 26,6 26,27 0,27 8,16" fill="var(--brand-sky)"/>
        <polygon points="196,6 170,6 170,27 196,27 188,16" fill="var(--brand-sky)"/>
        <polygon points="16,22 26,22 26,27" fill="#0a6d9c"/>
        <polygon points="180,22 170,22 170,27" fill="#0a6d9c"/>
        <rect x="16" y="0" width="164" height="22" fill="var(--brand-blue)"/>
      </svg>
      <div class="ribbon-text">ARTICLE 1 : General</div>
    </div>
    <div class="body" style="top:133px">
      <div class="section"><h3>1.1: Name</h3>
        <p>This organization is incorporated under the laws of the State of Westmoor and shall be known as the Brackenvale Area Chamber of Commerce (“Chamber”).</p></div>
      <div class="section"><h3>1.2: Purpose</h3>
        <p>The Brackenvale Area Chamber of Commerce is organized to build a strong community where businesses can thrive by fostering</p>
        <ul class="points">
          <li><h4>Positive Connections</h4>Meaningful connections that help our business community thrive, and connect our members with customers, partners, mentors and friends.</li>
          <li><h4>Business Growth</h4>The growth of local businesses through effective promotion and business development opportunities.</li>
          <li><h4>Community Engagement</h4>Community engagement through programs and events, we can influence the culture of our community and enhance the quality of life.</li>
          <li><h4>Collaborative Advocacy</h4>Advocacy for a healthy economy and aligning businesses and government, we provide a voice for initiatives relevant to our members.</li>
        </ul></div>
      <div class="section"><h3>1.3: Service Area</h3>
        <p>The service area of the Chamber includes the region of Brackenvale, which includes, Fernhollow, Saltmere, Harbor Glen, and Wendlow. The service area may also include Brackenvale County and areas beyond.</p></div>
      <div class="section"><h3>1.4: Limitation of Methods</h3>
        <p>The Chamber shall observe all local, state and federal laws, rules, and regulations that apply to a non-profit business incorporated under Westmoor Revised Statute Chapter 65 and exempt from income tax under Section 501(c)(6) of the Internal Revenue Code. The Chamber shall comply with Internal Revenue Code section 501(c)(6) and rules and regulations thereunder prior to lending its influence or facilities, either directly or indirectly, to the nomination, election, or appointment of any candidate for public office or engaging in legislative activities on a federal or state-wide basis.</p></div>
    </div>
    <footer class="footer-band"><span>P : (555) 014-2290 &nbsp;|&nbsp; W : www.brackenvalecouncil.org</span><span>2</span></footer>
  </section>
  <div class="page-label page-label--top page-label--right">PAGE - 02</div>

  <!-- Page 3 -->
  <section class="page page--three">
    <div class="top-band"></div>
    <div class="ribbon" style="top:39px">
      <svg width="196" height="28" viewBox="0 0 196 28" aria-hidden="true">
        <polygon points="0,6 26,6 26,27 0,27 8,16" fill="var(--brand-sky)"/>
        <polygon points="196,6 170,6 170,27 196,27 188,16" fill="var(--brand-sky)"/>
        <polygon points="16,22 26,22 26,27" fill="#0a6d9c"/>
        <polygon points="180,22 170,22 170,27" fill="#0a6d9c"/>
        <rect x="16" y="0" width="164" height="22" fill="var(--brand-blue)"/>
      </svg>
      <div class="ribbon-text">ARTICLE 2 : Membership</div>
    </div>
    <div class="body" style="top:92px">
      <div class="section"><h3>2.1: Eligibility</h3>
        <p>Any person, association, corporation, partnership, government division or subdivision, entity, or estate having an interest in the objectives of the Chamber shall be eligible to apply for membership. No single person, association, corporation, partnership, government division or subdivision, entity, or estate may apply for more than one membership.</p></div>
      <div class="section"><h3>2.2: Classes of Membership and Voting Rights</h3>
        <p>The Chamber shall have two classes of membership. The designation of such classes and the qualifications and rights of membership of such classes shall be as follows:</p>
        <ul class="points">
          <li><h4>Active Membership</h4>Any association, business, corporation, partnership, government division or subdivision, entity, or estate shall be eligible to be admitted as an active member. Active members are entitled to vote to elect the Board of Directors and on all matters that the Board of Directors makes subject to vote by members.</li>
          <li><h4>Affiliate Members</h4>All individuals, including but not limited to retired persons, persons holding public office, educators, ministers, and non-business owners shall be eligible for affiliate membership. Affiliate members are not entitled to vote.</li>
        </ul>
        <div class="sub"><h4>2.2.1 Rights of Voting Members</h4>
          <p>A person shall become a voting member of the corporation by submitting an application for membership and, if eligible and accepted, paying an annual due as determined and specified by the board of directors. Said membership, as outlined in Section X, must be qualified as an active membership as per the bylaws of the Chamber. An active member shall be entitled to:<br>(a) Vote to elect members of the board<br>(b) Serve on the Board of Directors, if elected.<br>(c) Serve on a board committee, if appointed by the board.<br>Every qualified voting member shall be entitled to one and only one vote in any organizational matters</p></div></div>
      <div class="section" style="margin-top:10px"><h3>2.3: Application</h3>
        <p>Application for membership shall be submitted through the Chamber's website or by paper application at the Chamber office.</p>
        <p>The Board of Directors may from time to time prescribe or modify the content of the application, as well as dues associated with each type of membership, but if not so prescribed, such application shall contain the name, physical address, mailing address, email address, and telephone number of such prospective member and, if the application is one for active membership, the individual authorized as the voting representative for the prospective member.</p></div>
    </div>
    <footer class="footer-band"><span>P : (555) 014-2290 &nbsp;|&nbsp; W : www.brackenvalecouncil.org</span><span>3</span></footer>
  </section>
  <div class="page-label page-label--bottom page-label--left">PAGE - 03</div>

  <!-- Page 4 -->
  <section class="page page--four">
    <div class="top-band"></div>
    <div class="ribbon" style="top:39px">
      <svg width="196" height="28" viewBox="0 0 196 28" aria-hidden="true">
        <polygon points="0,6 26,6 26,27 0,27 8,16" fill="var(--brand-sky)"/>
        <polygon points="196,6 170,6 170,27 196,27 188,16" fill="var(--brand-sky)"/>
        <polygon points="16,22 26,22 26,27" fill="#0a6d9c"/>
        <polygon points="180,22 170,22 170,27" fill="#0a6d9c"/>
        <rect x="16" y="0" width="164" height="22" fill="var(--brand-blue)"/>
      </svg>
      <div class="ribbon-text">ARTICLE 2 : Membership</div>
    </div>
    <div class="body" style="top:84px">
      <div class="section"><h3>2.4: Acceptance</h3>
        <p>Acceptance of members shall be made by the Board of Directors at the next regular Board meeting, after receipt of an application for membership. Any acceptance of an applicant for membership is made on the condition that the applicant accepts the terms and conditions of membership and agrees to abide by these bylaws.</p></div>
      <div class="section"><h3>2.5: Denial and Revocation of Application</h3>
        <p>Denial or revocation of any application for membership must be based on cause and shall be determined by the Board of Directors in an executive session, after an evaluation of the applicant’s ability and willingness to abide by the purposes of the Chamber, the terms and conditions of membership, and these bylaws. Matters considered by the Board in making their determination shall be recorded, sealed and maintained by the Secretary of the Board. A two-thirds majority is required to deny or revoke an application or membership. If an application for membership is denied, the Chamber shall return to the applicant all dues, if any, that the applicant paid with the submission of the application. If a membership is revoked, all dues paid shall not be refunded.</p></div>
      <div class="section"><h3>2.6: Membership Dues</h3>
        <p>Dues for active and affiliate members shall be at such rate or rates, schedule or formula as prescribed by the Board. The Board may modify all such dues as it deems appropriate upon a majority vote. Annual membership dues are billed annually and due 30 days after invoiced.</p></div>
      <div class="section"><h3>2.7: Terms &amp; Conditions</h3>
        <p>The terms and conditions of membership of the Chamber are designed to maintain the good reputation of the Chamber and it’s membership. Membership of the Chamber is a privilege and not a right, and the Chamber shall consider new and continued membership on a case-by-case basis. Membership may be revoked or denied for actions not in accordance with the Chamber’s purposes, including but not limited to the following:</p>
        <ul class="tight">
          <li>Fraudulent business activities.</li>
          <li>Untruthful, fabricated or deceptive information on membership applications.</li>
          <li>Repeated consumer complaints that are made in good faith and supported by substantial evidence.</li>
          <li>Findings by any government subdivision, consumer advocate or watchdog group, or the Fair Trade Bureau of Westmoor of irregular, false, criminal or deceitful business practices.</li>
          <li>Practices or activities by the member as either a current or past business owner.</li>
          <li>Using the Chamber or its name for subversive, deceitful or illegal activities, or for any other activities that, in the Board of Directors’ sole opinion, may ultimately harm the reputation of the Chamber.</li>
          <li>Harassment of Chamber members via marketing solicitations.</li>
          <li>Disruptive or offensive behavior at Chamber meetings.</li>
          <li>Threats of violence to the Chamber staff or its members.</li>
        </ul></div>
    </div>
    <footer class="footer-band"><span>P : (555) 014-2290 &nbsp;|&nbsp; W : www.brackenvalecouncil.org</span><span>4</span></footer>
  </section>
  <div class="page-label page-label--bottom page-label--right">PAGE - 04</div>

</div>
</body>
</html>
```